Kestrel Finish Studio (KFS)

I would like to design a dedicated site for my KFS product, which allows industry employees to be trained in the visual inspection of mechanical parts. My product is a 3D simulator (see https://morvint-works.ch/our-applications/virtual-reality/ and https://morvint-works.ch for videos) which makes it possible to manufacture standard parts representative of a type of defect which is accepted or refused by the quality department. These master parts can be used to create a common quality culture in the company and to train employees in a homogeneous way. The simulator is initially designed for watchmaking, but must be designed for much broader industries (cars, phone reconditioning, ball bearings, etc.)
L'information que j'ai donnée n'est pas assez précise. Je dois préciser les domaines métiers visés par le site internet. J'ai besoin de quelques jours pour choisir les domaines les plus représentatifs.
Coded - Design and coding required
1 page

```html
<!DOCTYPE html>
<html lang="en">
<head>
<meta charset="utf-8">
<title>Kestrel Finish Studio</title>
<link rel="stylesheet" href="https://fonts.googleapis.com/css2?family=Playfair+Display:wght@700&family=Lora:wght@400;600&family=Mulish:wght@400;600;700&display=swap">
<style>
:root{
  --blue:#0f6fb9;
  --blue-dark:#0b5d9e;
  --navy:#182030;
  --ink:#222831;
  --text:#3c4048;
  --light-bg:#f4f3f3;
  --white:#ffffff;
  --line:#3b8fd0;
}
*{margin:0;padding:0;box-sizing:border-box}
html,body{width:1200px;height:3155px;overflow:hidden}
body{position:relative;background:var(--white);font-family:'Mulish',sans-serif;color:var(--text)}
.abs{position:absolute}
/* header */
.site-header{position:absolute;left:0;top:0;width:1200px;height:85px;background:var(--white)}
.brand{position:absolute;left:135px;top:26px;font-family:'Playfair Display',serif;font-weight:700;font-size:22px;color:var(--ink)}
.nav{position:absolute;top:28px;left:571px;display:flex;gap:0;font-size:14px;color:var(--ink)}
.nav a{display:block;height:28px;line-height:28px;padding:0 12px;border-radius:14px;text-decoration:none;color:var(--ink);margin-right:9px}
.nav a.active{background:var(--blue);color:var(--white)}
/* hero */
.hero{position:absolute;left:0;top:85px;width:1200px;height:483px;
  background:radial-gradient(ellipse at 35% 45%,#8a7a62 0%,#4d4233 35%,#2b241c 70%,#1c1712 100%)}
.hero-panel-outline{position:absolute;left:692px;top:201px;width:520px;height:241px;border:2px solid var(--line);border-right:none;border-radius:80px 0 0 80px}
.hero-panel{position:absolute;left:703px;top:212px;width:497px;height:220px;background:var(--blue);border-radius:70px 0 0 70px}
.hero-title{position:absolute;left:766px;top:238px;font-family:'Playfair Display',serif;font-weight:700;font-size:39px;line-height:46px;color:var(--white)}
.hero-sub{position:absolute;left:766px;top:347px;font-size:15px;line-height:22px;font-weight:600;color:var(--white);letter-spacing:.2px}
.dots{position:absolute;left:566px;top:530px;display:flex;gap:5px}
.dots i{width:9px;height:9px;border-radius:50%;background:var(--white)}
.dots i.on{background:var(--blue)}
/* generic */
.heading{font-family:'Lora',serif;font-weight:600;text-transform:uppercase;color:var(--ink);font-size:17px;line-height:29px}
.rule{width:40px;height:2px;background:var(--blue)}
.btn{display:block;text-align:center;background:var(--blue);color:var(--white);font-weight:700;border-radius:22px;text-transform:uppercase}
.photo{position:absolute}
/* control */
.control-photo{left:136px;top:624px;width:479px;height:397px;background:linear-gradient(135deg,#cfd3d6,#b9aea0 50%,#8d8479)}
.control-text{position:absolute;left:655px;top:622px;width:415px}
.control-text p{font-size:12.8px;line-height:18px;color:var(--text);margin-bottom:19px}
/* components */
.components{position:absolute;left:0;top:1079px;width:1200px;height:461px;background:var(--navy)}
.components-photo{left:600px;top:0;width:600px;height:461px;background:linear-gradient(90deg,var(--navy) 0%,#5b4632 25%,#b98a55 55%,#8a6a48 80%,#5a4636 100%)}
.components-text{position:absolute;left:131px;top:46px;width:442px;color:var(--white)}
.components-text .heading{color:var(--white);font-size:17.5px}
.components-text .rule{background:var(--white);margin:16px 0 36px}
.components-text p{font-size:14.5px;line-height:22.5px;text-align:justify;color:#e8ebef;margin-bottom:22px}
/* simulator */
.sim-photo{left:131px;top:1598px;width:481px;height:386px;background:linear-gradient(90deg,#0c3a5e 0 27%,#050505 27% 100%)}
.sim-text{position:absolute;left:674px;top:1634px;width:390px}
.sim-text p{font-size:12.8px;line-height:20.8px;text-align:justify;margin-top:34px}
/* cards */
.features{position:absolute;left:0;top:2050px;width:1200px;height:472px;background:var(--light-bg)}
.card{position:absolute;top:58px;width:298px;height:341px;border:1px solid var(--line);background:var(--white);text-align:center}
.card svg{display:block;margin:38px auto 0}
.card h3{font-family:'Lora',serif;font-weight:600;font-size:16px;line-height:24px;color:var(--ink);text-transform:uppercase;margin-top:28px}
.card p{font-size:12.6px;line-height:19.3px;padding:0 40px;margin-top:16px}
.card .btn{position:absolute;left:98px;bottom:-18px;width:102px;height:34px;line-height:34px;font-size:11px;border-radius:17px}
/* awareness */
.awareness{position:absolute;left:0;top:2522px;width:1200px;height:296px;background:radial-gradient(ellipse at 60% 50%,#1a7fcb 0%,#0f6fb9 55%,#0b5e9f 100%);text-align:center;color:var(--white)}
.awareness h2{font-family:'Lora',serif;font-weight:600;font-size:17px;text-transform:uppercase;margin-top:66px}
.awareness p{font-size:15px;line-height:21.5px;width:880px;margin:18px auto 0}
.awareness .btn{background:var(--white);color:var(--blue);width:102px;height:32px;line-height:32px;font-size:12px;border-radius:16px;margin:24px auto 0}
/* footer */
.site-footer{position:absolute;left:0;top:2818px;width:1200px;height:337px;background:var(--navy);color:var(--white)}
.footer-brand{position:absolute;left:142px;top:103px;font-family:'Lora',serif;font-size:27px;line-height:30px}
.footer-col{position:absolute;top:48px}
.footer-col h4{font-size:13px;font-weight:700;letter-spacing:.5px;margin-bottom:24px}
.contact-item{position:relative;padding-left:34px;font-size:12.5px;line-height:16px;margin-bottom:19px}
.contact-item .ico{position:absolute;left:0;top:2px;width:24px;height:24px;border-radius:50%;background:var(--blue)}
.contact-item .ico svg{display:block;margin:5px auto}
.menu li{list-style:none;font-size:12.5px;line-height:16px;margin-bottom:8px;text-transform:uppercase}
.social-item{position:relative;padding-left:34px;font-size:12.3px;line-height:16px;margin-bottom:18px}
.social-item .ico{position:absolute;left:0;top:3px;width:22px;height:22px;border-radius:50%;background:var(--blue)}
.footer-rule{position:absolute;left:135px;top:260px;width:935px;height:1px;background:#34405a}
.copyright{position:absolute;left:0;top:296px;width:1200px;text-align:center;font-size:11px}
</style>
</head>
<body>

<header class="site-header">
  <div class="brand">Kestrel Finish Studio</div>
  <nav class="nav">
    <a class="active">Home</a><a>About us</a><a>Services</a><a>References</a><a>Blog</a><a>Contact Us</a>
  </nav>
</header>

<section class="hero" role="img" aria-label="Watchmaker holding tweezers over an open watch movement on a workbench"></section>
<div class="hero-panel-outline"></div>
<div class="hero-panel"></div>
<h1 class="hero-title">Kestrel Finish<br>Studio</h1>
<p class="hero-sub">VIRTUAL REALITY AT THE SERVICE OF<br>CONTROLLED AESTHETIC WATCHMAKING</p>
<div class="dots"><i></i><i></i><i class="on"></i><i></i><i></i></div>

<div class="photo control-photo" role="img" aria-label="Hand with a screwdriver working on a watch movement held in a blue holder"></div>
<div class="control-text">
  <h2 class="heading">How to control it?</h2>
  <div class="rule" style="margin:12px 0 30px"></div>
  <p>Adopting a simple and unambiguous language for a common understanding of aesthetic quality at the extended enterprise level.</p>
  <p>By using a semantic reference matrix associating the types of anomalies (scratches, marks, deformations, stains, etc.) with the intensity levels defined with the company.</p>
  <p>Determining the compliance thresholds of the component or product.</p>
  <p>Providing uniform training in operational competence for those responsible for aesthetic control.</p>
  <p>By designing realistic and attractive teaching sequences for total quality control.</p>
  <p style="margin-top:23px">By regularly assessing the competence to measure the aesthetics, expressed in a tangible, reliable and sustainable way (R&amp;R), of a component or product.</p>
</div>

<section class="components">
  <div class="photo components-photo" role="img" aria-label="Watchmaker's hands with screwdrivers beside an open watch movement in warm light"></div>
  <div class="components-text">
    <h2 class="heading">Lighten the management of<br>physical components</h2>
    <div class="rule"></div>
    <p>Companies must manage and maintain sets of physical components used as a &nbsp;"yardstick" for the training of aesthetic testers. The cost of managing a set of physical parts representing all combinations of shapes, defect types, materials and finishes is very high.</p>
    <p>KFS allows the company to significantly reduce its management burden by scanning components or products in 3D and then virtually adding 'typical' aesthetic anomalies.</p>
    <a class="btn" style="width:128px;height:41px;line-height:41px;font-size:13px;margin-top:20px;margin-left:3px">Read more</a>
  </div>
</section>

<div class="photo sim-photo" role="img" aria-label="Simulator software window with a settings panel and a 3D golden watch ring"></div>
<div class="sim-text">
  <h2 class="heading">Kestrel Finish Studio</h2>
  <div class="rule" style="margin-top:20px"></div>
  <p>Kestrel Finish Studio has developed, in collaboration with the Lakeside watchmaking school, a fault simulator on a mechanical part. This allows teachers to train students in more depth in the profession of quality controller. This tool combined with an LMS (Learning Management System) or the integrated management interface makes it possible to animate aesthetic control training in a fun and efficient way.</p>
  <a class="btn" style="width:128px;height:41px;line-height:41px;font-size:13px;margin-top:32px;margin-left:2px">Read more</a>
</div>

<section class="features">
  <article class="card" style="left:130px">
    <svg width="70" height="70" viewBox="0 0 70 70" fill="none" stroke="var(--blue)" stroke-width="2.5" stroke-linecap="round">
      <circle cx="35" cy="35" r="31"/><circle cx="35" cy="35" r="26"/>
      <path d="M35 9v5M61 35h-5M35 61v-5M9 35h5"/>
      <path d="M35 35l18-18"/><circle cx="35" cy="35" r="3"/>
      <rect x="20" y="37" width="10" height="7"/>
    </svg>
    <h3>Improve after-sales<br>service returns</h3>
    <p>to assist them in the objective assessment of aesthetic defects by referring to the semantic matrix as well as to the cases already referenced.</p>
    <a class="btn">Read more</a>
  </article>
  <article class="card" style="left:451px">
    <svg width="70" height="70" viewBox="0 0 70 70" fill="none" stroke="var(--blue)" stroke-width="2.5" stroke-linecap="round" stroke-linejoin="round">
      <path d="M12 3h34v64H12z"/>
      <path d="M18 14l3 3 5-6M18 28l3 3 5-6M18 42l3 3 5-6"/>
      <path d="M31 15h10M31 29h10M31 43h10"/>
      <circle cx="52" cy="18" r="9"/><path d="M52 27v14"/>
      <circle cx="22" cy="56" r="5"/><path d="M31 57h8"/>
    </svg>
    <h3>Improving the total<br>quality approach</h3>
    <p>During the entire product life cycle, from design through customer service to distribution, the KFS application makes it possible to build up a database of aesthetic defects in a simple,</p>
    <a class="btn">Read more</a>
  </article>
  <article class="card" style="left:770px">
    <svg width="70" height="70" viewBox="0 0 70 70" fill="none" stroke="var(--blue)" stroke-width="3" stroke-linecap="round" stroke-linejoin="round">
      <path d="M12 3h34l13 13v51H12z"/><path d="M46 3v13h13"/>
      <path d="M19 28l3 3 5-6M19 42l3 3 5-6M19 56l3 3 5-6"/>
      <path d="M33 30h18M33 44h18M33 58h18"/>
    </svg>
    <h3>A semantic matrix of<br>aesthetic defects</h3>
    <p>KFS is based on a semantic matrix that defines 5 levels of intensity for each of the 5 types of aesthetic defects referenced: Scratches - Marks - Deformations - Stains - Uniformity.</p>
    <a class="btn">Read more</a>
  </article>
</section>

<section class="awareness">
  <h2>Raising awareness of criteria and aesthetic vocabulary</h2>
  <p>Aesthetic defects are often the result of careless handling of the components and products concerned, whether during manufacture, assembly or marketing. By making the KFS platform available to staff in direct contact with the product, it becomes very easy to make them aware of the evaluation criteria and the aesthetic vocabulary defined by the company.</p>
  <a class="btn">Read more</a>
</section>

<footer class="site-footer">
  <div class="footer-brand">Kestrel Finish<br>Studio</div>
  <div class="footer-col" style="left:422px">
    <h4>CONTACT US</h4>
    <div class="contact-item"><span class="ico"><svg width="14" height="14" viewBox="0 0 14 14"><path d="M7 1a4 4 0 0 1 4 4c0 3-4 8-4 8S3 8 3 5a4 4 0 0 1 4-4z" fill="#fff"/><circle cx="7" cy="5" r="1.5" fill="var(--blue)"/></svg></span>Unit 4, Level 2 North,<br>17-21 Alder Lane, Brookfield 4020.</div>
    <div class="contact-item"><span class="ico"><svg width="14" height="14" viewBox="0 0 14 14"><path d="M3 1.5l2.5 0 1 3-1.5 1.2a7 7 0 0 0 3.3 3.3L9.5 7.5l3 1V11c0 .8-.7 1.5-1.5 1.5A10 10 0 0 1 1.5 3c0-.8.7-1.5 1.5-1.5z" fill="#fff"/></svg></span>Call Us<br>+1 555 014 2270</div>
    <div class="contact-item"><span class="ico"><svg width="14" height="14" viewBox="0 0 14 14"><rect x="1.5" y="3" width="11" height="8" rx="1" fill="#fff"/><path d="M2 3.5l5 4 5-4" stroke="var(--blue)" stroke-width="1.2" fill="none"/></svg></span>E mail Us<br>info@kestrelfinishstudio.com</div>
  </div>
  <div class="footer-col" style="left:775px">
    <h4>MENU</h4>
    <ul class="menu"><li>Home</li><li>About us</li><li>Services</li><li>References</li><li>Blog</li><li>Contact us</li></ul>
  </div>
  <div class="footer-col" style="left:971px">
    <h4>FOLLOW US</h4>
    <div class="social-item"><span class="ico"></span>Like us on<br>CIRCLEBOARD</div>
    <div class="social-item"><span class="ico"></span>Follow us on<br>CHIRPLINE</div>
    <div class="social-item"><span class="ico"></span>Follow us on<br>WORKNET</div>
  </div>
  <div class="footer-rule"></div>
  <div class="copyright">Copyright © 2023 All Rights Reserved</div>
</footer>

</body>
</html>
```